Playful Website Design Needed Pet Sitting and Dog Walking Business

Need a simple one page Web Design Built on WordPress.
Sections:

About Us
Services Provided
Costs
Contact Us
Intake Form (Questionnaire that goes to email)
See us in Action

Industry/Entity Type

Pet Sitting and Dog Walking

Number of Pages Required

1 page

Font styles to use
Other font styles liked:
• See the Business Card Font and use that.

Colors
EE7325
F08F49
F5BC92
FAE3D3
FDF4ED

Requirements
Must have
• See attached Logo Design, with Font's and Colors Use these as theme guide

```html
<!DOCTYPE html>
<html lang="en">
<head>
<meta charset="utf-8">
<title>Paws Together Care – Pet Sitting and Dog Walking</title>
<link rel="stylesheet" href="https://fonts.googleapis.com/css2?family=Yanone+Kaffeesatz:wght@300;400&family=Tinos:wght@400;700&family=Roboto:wght@400;700&display=swap">
<style>
:root{
  --orange:#f04e0c;
  --orange-deep:#e2480e;
  --orange-soft:#f08f49;
  --yellow:#ffe000;
  --green:#6bb531;
  --dark:#131313;
  --ink:#1c1c1c;
  --muted:#555;
  --paper:#e7e5e2;
  --white:#fff;
}
*{box-sizing:border-box;margin:0;padding:0}
html,body{width:1200px;height:5181px;overflow:hidden}
body{position:relative;font-family:"Tinos",serif;color:var(--ink);background:var(--white)}
.abs{position:absolute}
.btn{display:inline-block;background:var(--orange);color:#fff;font:700 11px "Tinos",serif;text-transform:uppercase;border-radius:20px;padding:12px 30px;letter-spacing:.3px;white-space:nowrap}
.ph{position:absolute}
.divider{position:absolute;left:50%;transform:translateX(-50%);width:120px;height:16px}
.divider::before,.divider::after{content:"";position:absolute;top:7px;width:44px;height:2px;background:var(--green)}
.divider::before{left:0}.divider::after{right:0}
.divider span{position:absolute;left:52px;top:0;width:16px;height:16px;border-radius:50%;background:var(--orange-soft)}
.sec-title{position:absolute;left:0;width:1200px;text-align:center;font-family:"Yanone Kaffeesatz",sans-serif;font-weight:300;font-size:40px;white-space:nowrap}

/* header */
.topbar{top:0;left:0;width:1200px;height:70px}
.topbar .contact{position:absolute;top:24px;font-size:15px;color:#333;white-space:nowrap}
.ico{display:inline-block;vertical-align:-3px;margin-right:16px}
.seeus{position:absolute;left:953px;top:16px;background:var(--orange);color:#fff;font:700 12px "Tinos",serif;border-radius:18px;width:117px;height:34px;line-height:34px;text-align:center}
.navbar{top:70px;left:0;width:1200px;height:48px;background:var(--orange)}
.navbar a{position:absolute;top:16px;color:#fff;font:700 12px "Tinos",serif;text-transform:uppercase;text-decoration:none;white-space:nowrap}
.navbar a.active{border-bottom:2px solid #fff;padding-bottom:3px}
.logo{top:0;left:110px;width:270px;height:160px;z-index:3}
.logo .dot{position:absolute;left:98px;top:8px;width:44px;height:44px;border-radius:50%;background:var(--orange-soft)}
.logo .name{position:absolute;left:10px;top:58px;width:220px;text-align:center;font:300 34px/34px "Yanone Kaffeesatz",sans-serif;color:var(--green)}

/* hero */
.hero{top:118px;left:0;width:1200px;height:650px}
.hero h1{position:absolute;left:128px;top:135px;color:#fff;font:300 66px/68px "Yanone Kaffeesatz",sans-serif}
.hero p{position:absolute;left:128px;top:282px;width:340px;color:#fff;font-size:17px;line-height:26px}
.hero .btn{position:absolute;left:128px;top:385px}

/* services */
.card{position:absolute;top:957px;width:448px;height:343px;border-radius:12px;overflow:hidden;background:var(--green)}
.card .img{position:absolute;left:0;top:0;width:448px;height:235px}
.card .badge{position:absolute;left:30px;top:250px;width:70px;height:70px;border-radius:50%;background:var(--orange);border:3px solid #fff}
.card h3{position:absolute;left:128px;top:250px;color:#fff;font:300 24px "Yanone Kaffeesatz",sans-serif}
.card p{position:absolute;left:128px;top:282px;width:200px;color:#fff;font-size:10px;line-height:13px}
.card .btn{position:absolute;right:0;top:278px;padding:9px 18px;font-size:10px;border-radius:18px 0 0 18px}

/* about */
.about{top:1400px;left:0;width:1200px;height:830px;background:var(--dark)}
.about .about-title{color:#fff;top:142px}
.about .circle{position:absolute;left:142px;top:270px;width:440px;height:440px;border-radius:50%;background:var(--yellow)}
.about .circle div{position:absolute;left:14px;top:14px;width:412px;height:412px;border-radius:50%;background:linear-gradient(160deg,#7a8a55,#4a4332 60%,#9a7b4a)}
.about .lead-title{position:absolute;left:680px;top:262px;color:#fff;font:400 31px/40px "Tinos",serif;white-space:nowrap}
.about .lead-text{position:absolute;left:680px;top:365px;width:400px;color:#ddd;font:400 12.5px/22.5px "Roboto",sans-serif}
.about .btn{position:absolute;left:680px;top:632px}

/* costs */
.costs{top:2230px;left:0;width:1200px;height:640px;background:var(--paper)}
.costs h2{position:absolute;left:128px;top:205px;font:300 66px/68px "Yanone Kaffeesatz",sans-serif;color:var(--ink)}
.costs p{position:absolute;left:130px;top:352px;width:330px;font-size:17px;line-height:26px}
.costs .btn{position:absolute;left:130px;top:453px}

/* blog */
.post{position:absolute;top:3055px;width:222px;height:348px;background:#fff;box-shadow:0 2px 10px rgba(0,0,0,.1)}
.post .img{height:172px}
.post .date{margin:20px 0 0 22px;font-size:9px;color:var(--orange)}
.post h4{margin:14px 22px 0;font-size:9.5px;line-height:15px;font-weight:700}
.post p{margin:8px 22px 0;font-size:9.5px;line-height:14px;color:#444}
.post a{display:block;margin:8px 22px 0;font-size:9px;color:var(--ink)}
.dots{position:absolute;width:70px;height:150px;background-image:radial-gradient(#ccc 1.2px,transparent 1.3px);background-size:12px 12px}

/* testimonials */
.testi{top:3487px;left:0;width:1200px;height:545px;background:linear-gradient(90deg,#e85512,#f06a22 50%,#e65816)}
.testi .sec-title{color:#fff;top:70px}
.testi .box{position:absolute;left:131px;top:160px;width:938px;height:302px;background:#fff}
.review{position:absolute;top:30px;width:260px}
.review .av{position:absolute;left:0;top:0;width:64px;height:64px;border-radius:50%;background:#c9a894;border:2px solid #eee}
.review .who{position:absolute;left:84px;top:10px;font-size:11px;line-height:16px;white-space:nowrap}
.review .stars{position:absolute;left:84px;top:44px;color:var(--orange);font-size:12px;letter-spacing:1px}
.review p{position:absolute;left:0;top:100px;width:240px;font-size:10.5px;line-height:19px;color:#555}
.review .q{position:absolute;font:700 48px "Tinos",serif;color:#ececec}

/* contact */
.contact-wrap{top:4035px;left:0;width:1200px;height:725px}
.cbox{position:absolute;left:131px;top:283px;width:938px;height:410px;background:var(--yellow);border-radius:20px}
.cbox h2{position:absolute;left:0;width:938px;top:60px;text-align:center;font:300 36px "Yanone Kaffeesatz",sans-serif}
.field{position:absolute;height:36px;background:#fff;font-size:9px;color:#555;padding:12px 20px}
.field i{position:absolute;right:10px;top:11px;width:12px;height:12px;border:1px solid #ccc;border-radius:2px}
.cbox .btn{position:absolute;left:402px;top:345px;width:134px;text-align:center;padding:11px 0}

/* footer */
.footer{top:4760px;left:0;width:1200px;height:421px;background:#0b0b0b;color:#fff}
.footer h5{position:absolute;top:40px;font:700 18px "Tinos",serif}
.footer ul{position:absolute;top:88px;list-style:none;font:700 10px/21px "Tinos",serif}
.fitem{position:absolute;font-size:11px;line-height:16px}
.fitem svg{position:absolute;left:-34px;top:2px}
.footer .nl p{font-size:11px;line-height:16px}
.social li{padding-left:22px;position:relative;line-height:24px}
.social li::before{content:"";position:absolute;left:0;top:6px;width:13px;height:13px;border-radius:50%;background:var(--green)}
.copy{position:absolute;top:378px;width:1200px;text-align:center;font-size:12px;color:#ddd}
</style>
</head>
<body>

<!-- header -->
<div class="abs topbar">
  <div class="contact" style="left:415px">
    <svg class="ico" width="16" height="16" viewBox="0 0 24 24"><path fill="#6bb531" d="M6.6 10.8a15.2 15.2 0 0 0 6.6 6.6l2.2-2.2c.3-.3.7-.4 1-.2 1.1.4 2.3.6 3.6.6.6 0 1 .4 1 1V20c0 .6-.4 1-1 1A17 17 0 0 1 3 4c0-.6.4-1 1-1h3.5c.6 0 1 .4 1 1 0 1.3.2 2.5.6 3.6.1.3 0 .7-.2 1z"/></svg>Call: +1 555-0142-7788
  </div>
  <div class="contact" style="left:664px">
    <svg class="ico" width="18" height="14" viewBox="0 0 24 18"><path fill="#6bb531" d="M0 0h24v18H0z"/><path fill="none" stroke="#fff" stroke-width="2" d="M1 1l11 9 11-9"/></svg>hello@pawstogethercare.com
  </div>
  <div class="seeus">SEE US</div>
</div>
<nav class="abs navbar">
  <a class="active" href="#" style="left:415px">Home</a>
  <a href="#" style="left:510px">About Us</a>
  <a href="#" style="left:632px">Services Provided</a>
  <a href="#" style="left:834px">Costs</a>
  <a href="#" style="left:935px">Contact Us</a>
</nav>

<!-- hero -->
<section class="abs hero">
  <div class="ph" role="img" aria-label="Dog walker leading a pack of dogs along an autumn path" style="left:0;top:0;width:1200px;height:650px;background:linear-gradient(120deg,#4d3a24,#8c6236 40%,#b17a3c 60%,#5e4a33)"></div>
  <svg class="ph" style="left:0;top:520px" width="1200" height="130" viewBox="0 0 1200 130" preserveAspectRatio="none">
    <path d="M0 80 Q300 10 600 60 Q900 110 1200 20 V130 H0Z" fill="#ffe000"/>
    <path d="M0 110 Q300 50 600 90 Q900 130 1200 60 V130 H0Z" fill="#6bb531"/>
    <path d="M0 120 Q300 75 600 112 Q900 140 1200 100 V130 H0Z" fill="#fff"/>
  </svg>
  <div class="ph" style="left:563px;top:560px;width:74px;height:74px;border-radius:50%;background:var(--orange-soft);border:4px solid var(--yellow)"></div>
  <h1>Pet Sitting<br>and Dog Walking</h1>
  <p>Sed ut perspiciatis unde omnis iste natus voluptatem accusantium doloremque laudantium, totam rem</p>
  <span class="btn">Learn More</span>
</section>

<!-- logo -->
<div class="abs logo">
  <svg class="ph" style="left:-60px;top:-10px" width="390" height="175" viewBox="0 0 390 175"><path d="M0 0H300 Q330 60 280 120 Q200 185 90 160 Q20 140 0 90Z" fill="#fff"/></svg>
  <div class="dot"></div>
  <div class="name">Paws Together Care</div>
</div>

<!-- services -->
<h2 class="sec-title" style="top:812px">Services Provided</h2>
<div class="divider" style="top:880px"><span></span></div>
<article class="card" style="left:129px">
  <div class="img" role="img" aria-label="Woman hugging a dog in a park" style="background:linear-gradient(140deg,#6b7b44,#4a3d2a 55%,#8a9a5a)"></div>
  <div class="badge"></div>
  <h3>Pet Sitting</h3>
  <p>Sed ut perspiciatis unde omnis iste natus voluptatem accusantium doloremque laudantium, totam rem</p>
  <span class="btn">Learn More</span>
</article>
<article class="card" style="left:623px">
  <div class="img" role="img" aria-label="Several dogs walking on leashes" style="background:linear-gradient(140deg,#9aa88a,#d8d6cc 45%,#6f5a3c)"></div>
  <div class="badge"></div>
  <h3>Dog Walking</h3>
  <p>Sed ut perspiciatis unde omnis iste natus voluptatem accusantium doloremque laudantium, totam rem</p>
  <span class="btn">Learn More</span>
</article>

<!-- about -->
<section class="abs about">
  <svg class="ph" style="left:0;top:0" width="1200" height="110" viewBox="0 0 1200 110" preserveAspectRatio="none">
    <rect width="1200" height="110" fill="#fff"/>
    <path d="M0 30 Q300 70 650 45 Q950 20 1200 25 V110 H0Z" fill="#ffe000"/>
    <path d="M0 40 Q300 85 650 60 Q950 40 1200 45 V110 H0Z" fill="#f04e0c"/>
    <path d="M0 70 Q250 40 600 80 Q950 110 1200 60 V110 H0Z" fill="#131313"/>
  </svg>
  <h2 class="sec-title about-title">About Paws Together Care</h2>
  <div class="divider" style="top:196px"><span></span></div>
  <div class="circle"><div role="img" aria-label="Woman walking a golden retriever on a park path"></div></div>
  <h3 class="lead-title">We are a Pet Sitting and<br>Dog Walking company</h3>
  <p class="lead-text">Sed ut perspiciatis unde omnis iste natus error sit voluptatem accusantium doloremque laudantium, totam rem aperiam, eaque ipsa quae ab illo inventore veritatis et quasi architecto beatae vitae dicta sunt explicabo. Nemo enim ipsam voluptatem quia voluptas sit aspernatur aut odit aut fugit, sed quia consequuntur magni dolores eos qui ratione voluptatem sequi nesciunt. Neque porro quisquam est, qui dolorem ipsum quia dolor sit amet, consectetur, adipisci velit, sed quia non numquam eius modi tempora incidunt ut labore et dolore magnam aliquam quaerat voluptatem. Ut enim ad minima veniam, quis nostrum exetionem ullam corporis suscipit laboriosam</p>
  <span class="btn">Learn More</span>
  <svg class="ph" style="left:0;top:770px" width="1200" height="60" viewBox="0 0 1200 60" preserveAspectRatio="none">
    <path d="M0 30 Q400 -5 800 25 Q1000 40 1200 20 V60 H0Z" fill="#ffe000"/>
    <path d="M0 40 Q400 10 800 40 Q1000 55 1200 35 V60 H0Z" fill="#f04e0c"/>
    <path d="M0 55 Q400 30 800 55 Q1000 62 1200 50 V60 H0Z" fill="#e7e5e2"/>
  </svg>
</section>

<!-- costs -->
<section class="abs costs">
  <h2>Costs<br>Pet Sitting</h2>
  <p>Sed ut perspiciatis unde omnis iste natus voluptatem accusantium doloremque laudantium, totam rem</p>
  <span class="btn">Learn More</span>
  <div class="ph" role="img" aria-label="Three dogs posed together over a green oval" style="left:490px;top:120px;width:580px;height:440px;border-radius:50%;background:radial-gradient(circle at 50% 60%,#5a4030,#6bb531 70%)"></div>
</section>

<!-- blog -->
<h2 class="sec-title" style="top:2925px">Latest Blog Posts</h2>
<div class="divider" style="top:2990px"><span></span></div>
<div class="dots" style="left:80px;top:3290px"></div>
<div class="dots" style="left:1050px;top:3290px"></div>
<article class="post" style="left:122px"><div class="img" role="img" aria-label="Walker with several dogs on a path" style="background:linear-gradient(135deg,#7d8a70,#c9b48e)"></div><div class="date">Jan 20, 2022</div><h4>NEMO ENIM IPSAM VOLUPTATEM QUIA VOLUPTAS SIT</h4><p>Sed ut perspiciatis unde omnis iste natus error sit voluptatem accusantium doloremque laudantium, totam rem aperiam, eaque ipsa quae ab illo</p><a>Learn More</a></article>
<article class="post" style="left:367px"><div class="img" role="img" aria-label="Two dogs close together" style="background:linear-gradient(135deg,#4a5a3a,#b07a44)"></div><div class="date">Jan 20, 2022</div><h4>NEMO ENIM IPSAM VOLUPTATEM QUIA VOLUPTAS SIT</h4><p>Sed ut perspiciatis unde omnis iste natus error sit voluptatem accusantium doloremque laudantium, totam rem aperiam, eaque ipsa quae ab illo</p><a>Learn More</a></article>
<article class="post" style="left:611px"><div class="img" role="img" aria-label="Pack of dogs at sunset" style="background:linear-gradient(135deg,#c99a5a,#6a4a30)"></div><div class="date">Jan 20, 2022</div><h4>NEMO ENIM IPSAM VOLUPTATEM QUIA VOLUPTAS SIT</h4><p>Sed ut perspiciatis unde omnis iste natus error sit voluptatem accusantium doloremque laudantium, totam rem aperiam, eaque ipsa quae ab illo</p><a>Learn More</a></article>
<article class="post" style="left:856px"><div class="img" role="img" aria-label="Dog walker on a street with dogs" style="background:linear-gradient(135deg,#6f8c5a,#b3b39a)"></div><div class="date">Jan 20, 2022</div><h4>NEMO ENIM IPSAM VOLUPTATEM QUIA VOLUPTAS SIT</h4><p>Sed ut perspiciatis unde omnis iste natus error sit voluptatem accusantium doloremque laudantium, totam rem aperiam, eaque ipsa quae ab illo</p><a>Learn More</a></article>

<!-- testimonials -->
<section class="abs testi">
  <h2 class="sec-title">Testimonials</h2>
  <div class="divider" style="top:134px"><span></span></div>
  <div class="box">
    <div class="review" style="left:40px"><div class="av" role="img" aria-label="Customer portrait"></div><div class="who">John Doe<br>Excepteur sint occaecat</div><div class="stars">★★★★★</div><span class="q" style="left:-20px;top:70px">“</span><p>Sed ut perspiciatis unde omnis iste natus error sit voluptatem accusantium doloremque laudantium, totam rem aperiam, eaque ipsa quae ab illo inventore veritatis et quasi architecto beatae vitae dicta sunt explicabo. Nemo enim ipsam voluptatem quia voluptas sit aspernatur aut odit aut fugit, sed quia consequuntur magni dolores eos qui ratione voluptatem sequi</p><span class="q" style="left:238px;top:220px">”</span></div>
    <div class="review" style="left:348px"><div class="av" role="img" aria-label="Customer portrait"></div><div class="who">John Doe<br>Excepteur sint occaecat</div><div class="stars">★★★★★</div><span class="q" style="left:-20px;top:70px">“</span><p>Sed ut perspiciatis unde omnis iste natus error sit voluptatem accusantium doloremque laudantium, totam rem aperiam, eaque ipsa quae ab illo inventore veritatis et quasi architecto beatae vitae dicta sunt explicabo. Nemo enim ipsam voluptatem quia voluptas sit aspernatur aut odit aut fugit, sed quia consequuntur magni dolores eos qui ratione voluptatem sequi</p><span class="q" style="left:238px;top:220px">”</span></div>
    <div class="review" style="left:656px"><div class="av" role="img" aria-label="Customer portrait"></div><div class="who">John Doe<br>Excepteur sint occaecat</div><div class="stars">★★★★★</div><span class="q" style="left:-20px;top:70px">“</span><p>Sed ut perspiciatis unde omnis iste natus error sit voluptatem accusantium doloremque laudantium, totam rem aperiam, eaque ipsa quae ab illo inventore veritatis et quasi architecto beatae vitae dicta sunt explicabo. Nemo enim ipsam voluptatem quia voluptas sit aspernatur aut odit aut fugit, sed quia consequuntur magni dolores eos qui ratione voluptatem sequi</p><span class="q" style="left:238px;top:220px">”</span></div>
  </div>
</section>

<!-- contact -->
<section class="abs contact-wrap">
  <svg class="ph" style="left:0;top:440px" width="1200" height="285" viewBox="0 0 1200 285" preserveAspectRatio="none">
    <path d="M0 30 Q600 110 1200 0 V285 H0Z" fill="#f04e0c"/>
    <path d="M0 45 Q600 115 1200 10 V285 H0Z" fill="#6bb531"/>
    <path d="M0 55 Q600 125 1200 30 V285 H0Z" fill="#0b0b0b"/>
  </svg>
  <div class="ph" role="img" aria-label="Three puppies peeking over the edge of the form" style="left:342px;top:55px;width:512px;height:235px;border-radius:120px 120px 0 0;background:linear-gradient(90deg,#2a2522,#a86a3c 50%,#5a4030)"></div>
  <div class="cbox">
    <h2>Paws Together Care Contact</h2>
    <div class="divider" style="top:115px"><span></span></div>
    <div class="field" style="left:125px;top:148px;width:340px">First name<i></i></div>
    <div class="field" style="left:474px;top:148px;width:340px">Phone<i></i></div>
    <div class="field" style="left:125px;top:198px;width:340px">Subject *<i></i></div>
    <div class="field" style="left:474px;top:198px;width:340px">Email address<i></i></div>
    <div class="field" style="left:125px;top:250px;width:689px;height:68px">Tell me something about you*<i></i></div>
    <span class="btn">Submit</span>
  </div>
</section>

<!-- footer -->
<footer class="abs footer">
  <h5 style="left:130px">Quick Links</h5>
  <ul style="left:130px"><li>About Us</li><li>Services Provided</li><li>Costs</li><li>Contact Us</li><li>Intake Form</li></ul>
  <h5 style="left:366px">Contact Us</h5>
  <div class="fitem" style="left:400px;top:90px;width:180px"><svg width="14" height="16" viewBox="0 0 24 24"><path fill="#fff" d="M12 2a7 7 0 0 0-7 7c0 5 7 13 7 13s7-8 7-13a7 7 0 0 0-7-7zm0 9.5A2.5 2.5 0 1 1 12 6.5a2.5 2.5 0 0 1 0 5z"/></svg>Paws Together Care<br>Level 1, 60 Nemo enim ipsum voluptatem quia voluptas sit</div>
  <div class="fitem" style="left:400px;top:150px"><svg width="14" height="14" viewBox="0 0 24 24"><path fill="#fff" d="M6.6 10.8a15.2 15.2 0 0 0 6.6 6.6l2.2-2.2c.3-.3.7-.4 1-.2 1.1.4 2.3.6 3.6.6.6 0 1 .4 1 1V20c0 .6-.4 1-1 1A17 17 0 0 1 3 4c0-.6.4-1 1-1h3.5c.6 0 1 .4 1 1 0 1.3.2 2.5.6 3.6.1.3 0 .7-.2 1z"/></svg>Call Us Today!<br>+1 555-0142-7788</div>
  <div class="fitem" style="left:400px;top:196px"><svg width="14" height="14" viewBox="0 0 24 24"><path fill="none" stroke="#fff" stroke-width="2" d="M3 21l3-1 12-12-2-2L4 18z"/></svg>Email Us<br>pawstogethercare.com</div>
  <h5 style="left:642px">Sign up for newsletter</h5>
  <div class="nl abs" style="left:642px;top:88px;width:300px">
    <p>Sign up with your email address to receive tips, news and updates!</p>
    <div style="margin-top:14px;width:293px;height:34px;border:1px solid #777;font-size:10px;padding:11px 16px">johndoe@email.com</div>
    <span class="btn" style="margin-top:16px;border-radius:0;width:155px;text-align:center;padding:11px 0">Subscribe</span>
  </div>
  <h5 style="left:992px">Social</h5>
  <ul class="social" style="left:992px;top:84px"><li>Video Channel</li><li>Community</li><li>Photo Feed</li><li>Pinboard</li></ul>
  <div class="copy">Paws Together Care © 2022. All Rights Reserved.</div>
</footer>

</body>
</html>
```